VELKO Website Redesign in Wix

Task:
Create a new design for all pages of the VELKO technology website in Wix. Specifications are:
Color palette preferences: black, white, gray, purple, blue. See VELKO Ref Doc provided.
Please refer to the VELKO_ref doc for a sample of the desired color palette
Typesetting must be in Montserrat
Brand will be that of a Marketing Technology company
Looking for vibrant, highly engaging images and organized, digestible flow. Open to suggestions
Required format is Wix.
VELKO logo does NOT need to be redesigned. Please use the files provided for the VELKO logo.
Look and feel
Each slider illustrates characteristics of the customer's brand and the style your logo design should communicate.

```html
<!DOCTYPE html>
<html lang="en">
<head>
<meta charset="utf-8">
<title>VELKO — Marketing Technology</title>
<link href="https://fonts.googleapis.com/css2?family=Montserrat:wght@500;600;700&family=Roboto:wght@400;500;700&display=swap" rel="stylesheet">
<style>
:root{
  --bg:#0b0630;
  --footer:#120a3d;
  --purple:#3d1c9e;
  --purple-dark:#1b0d55;
  --white:#ffffff;
  --text:#ecebf5;
  --muted:#d4d0e6;
  --orange:#cc450c;
  --line:#a9a6c2;
  --badge-ring:#d9d6e6;
}
*{box-sizing:border-box;margin:0;padding:0}
html,body{width:1200px;height:3235px;overflow:hidden}
body{
  position:relative;font-family:'Roboto',sans-serif;color:var(--text);
  -webkit-font-smoothing:antialiased;-moz-osx-font-smoothing:grayscale;
  background:
    radial-gradient(ellipse 520px 300px at 80px 760px,rgba(120,40,110,.22),transparent 70%),
    radial-gradient(ellipse 600px 260px at 1150px 1300px,rgba(40,60,160,.20),transparent 70%),
    radial-gradient(ellipse 700px 200px at 600px 1900px,rgba(70,30,140,.18),transparent 70%),
    radial-gradient(ellipse 500px 260px at 300px 2500px,rgba(60,30,130,.18),transparent 70%),
    var(--bg);
}
.abs{position:absolute}
h1,h2,h3{font-family:'Montserrat',sans-serif;color:var(--white)}
.section-title{font-size:26px;font-weight:700;line-height:1.3}
.btn{position:absolute;display:flex;align-items:center;justify-content:center;gap:10px;height:45px;padding:0 18px;background:var(--purple);color:var(--white);font:700 14px 'Roboto',sans-serif;text-transform:uppercase;border-radius:2px}
.btn svg{width:13px;height:13px}
.copy{font-size:15.5px;line-height:27.5px;text-align:justify;color:var(--text)}

.hero{left:0;top:0;width:1200px;height:625px;background:linear-gradient(90deg,#0d1433 0%,#161060 45%,#1b0b5a 72%,#120745 100%)}
.hero-visual{left:0;top:0;width:660px;height:625px;background:
  radial-gradient(circle at 330px 320px,rgba(240,140,70,.75) 0,rgba(190,90,70,.45) 60px,rgba(70,60,150,.25) 150px,transparent 260px),
  radial-gradient(circle at 400px 500px,rgba(200,120,100,.35) 0,transparent 120px),
  radial-gradient(circle at 200px 190px,rgba(30,120,140,.45) 0,transparent 110px),
  radial-gradient(circle at 480px 140px,rgba(30,120,140,.35) 0,transparent 110px),
  radial-gradient(circle at 150px 380px,rgba(30,110,140,.30) 0,transparent 120px),
  linear-gradient(90deg,#0c1430 0%,rgba(20,20,80,0) 100%)}
.logo{font-family:'Montserrat',sans-serif;font-weight:600;color:var(--white);letter-spacing:8px}
.nav{top:38px;left:395px;display:flex;gap:29px;font-size:14px;font-weight:700;color:var(--white)}
.welcome{left:627px;top:212px;font-size:20px;font-weight:700}
.hero-name{left:624px;top:235px;font-size:86px;font-weight:700;letter-spacing:1px;line-height:1.1}
.hero-lede{left:627px;top:338px;width:480px;font-size:15px;font-weight:500;line-height:26px;color:var(--white)}

.card{position:absolute;width:222px;height:251px;border-radius:14px;text-align:center;padding:22px 14px}
.card.filled{background:var(--purple)}
.card.dark{background:var(--purple-dark)}
.card svg{display:block;margin:0 auto;width:58px;height:54px}
.card h3{font:500 16px 'Roboto',sans-serif;margin-top:12px}
.card .rule{width:30px;height:2px;background:var(--white);margin:12px auto 13px}
.card p{font-size:14px;line-height:19px;color:var(--muted)}
.card .bar{width:160px;height:3px;background:var(--white);margin:20px auto 0}

.badge{position:absolute;top:1874px;width:148px;height:148px;background:var(--white);display:flex;align-items:center;justify-content:center}
.badge::after{content:"";width:64px;height:64px;border-radius:50%;border:3px solid var(--badge-ring)}
.partners{left:111px;top:2171px;width:976px;height:120px;display:flex;border:1px solid var(--line)}
.partner{flex:1;display:flex;align-items:center;justify-content:center;border-right:1px solid var(--line);font:600 21px 'Montserrat',sans-serif;color:#cfcbe0}
.partner:last-child{border-right:none}

.footer{left:0;top:2845px;width:1200px;height:390px;background:var(--footer)}
.f-head{font:700 13px 'Roboto',sans-serif;text-transform:uppercase;color:var(--white)}
.f-list{list-style:none;font-size:14px;line-height:34.5px;color:var(--white)}
.contact{font-size:16px;line-height:30px;color:var(--white)}
.social{display:flex;gap:10px}
.social span{width:31px;height:31px;border:1px solid var(--white);border-radius:50%}
</style>
</head>
<body>

<svg width="0" height="0" style="position:absolute">
  <symbol id="go" viewBox="0 0 14 14"><circle cx="7" cy="7" r="7" fill="#fff"/><path d="M5 4l3.5 3L5 10" stroke="#3d1c9e" stroke-width="2" fill="none"/></symbol>
</svg>

<section class="abs hero">
  <div class="abs hero-visual" role="img" aria-label="Hand holding a glowing smartphone surrounded by network and app icons"></div>
  <div class="abs logo" style="left:110px;top:20px;font-size:38px">VELKO</div>
  <nav class="abs nav"><span>Home</span><span>How it works</span><span>VELKO Applications</span><span>Company</span><span>Contact Us</span></nav>
  <div class="btn" style="left:935px;top:25px">Get Started <svg><use href="#go"/></svg></div>
  <h3 class="abs welcome">WELCOME TO</h3>
  <h1 class="abs hero-name">VELKO</h1>
  <p class="abs hero-lede">Increase and perfect your connection with consumers using VELKO™'s patented self-service content delivery technology</p>
  <div class="btn" style="left:627px;top:416px">Get Started <svg><use href="#go"/></svg></div>
</section>

<section>
  <h2 class="abs section-title" style="left:120px;top:806px;width:440px">STRATEGY TOWARDS MARKET DOMINANCE</h2>
  <p class="abs copy" style="left:120px;top:891px;width:412px">Lorem ipsum dolor sit amet, consectetur adipiscing elit, sed do eiusmod tempor incididunt ut labore et dolore magna aliqua. Ut enim ad minim veniam, quis nostrud exercitation ullamco laboris nisi ut aliquip ex ea commodo consequat. Duis aute irure dolor in reprehenderit in voluptate velit esse cillum dolore eu fugiat nulla pariatur. Excepteur sint occaecat cupidatat non proident, sunt in culpa qui officia deserunt mollit anim id est laborum.</p>
  <div class="btn" style="left:121px;top:1135px;width:152px">View All <svg><use href="#go"/></svg></div>

  <div class="card filled" style="left:609px;top:700px">
    <svg viewBox="0 0 58 54" aria-hidden="true"><circle cx="20" cy="13" r="10" fill="#fff"/><path d="M2 46c0-13 8-21 18-21s14 5 16 8v13z" fill="#fff"/><circle cx="42" cy="36" r="13" fill="#fff" stroke="#3d1c9e" stroke-width="3"/><path d="M42 29v14M35 36h14" stroke="#3d1c9e" stroke-width="3.5"/></svg>
    <h3>Corporate Subscription</h3><div class="rule"></div><p>Sed ut perspiciatis unde omnis iste natus error sit voluptatem accusantium</p><div class="bar"></div></div>
  <div class="card dark" style="left:858px;top:760px">
    <svg viewBox="0 0 58 54" aria-hidden="true"><rect x="6" y="4" width="46" height="34" fill="#fff"/><path d="M12 12h34M12 19h34M12 26h20" stroke="#1b0d55" stroke-width="3"/><circle cx="40" cy="36" r="8" fill="#fff" stroke="#1b0d55" stroke-width="3"/><path d="M35 43l-2 9 7-4 7 4-2-9" fill="#fff"/></svg>
    <h3>AD Tech Licensing</h3><div class="rule"></div><p>Sed ut perspiciatis unde omnis iste natus error sit voluptatem accusantium</p><div class="bar"></div></div>
  <div class="card dark" style="left:609px;top:983px">
    <svg viewBox="0 0 58 54" aria-hidden="true"><path d="M8 8h16a6 6 0 0 1 10 0h16v16a6 6 0 0 1 0 10v16H34a6 6 0 0 0-10 0H8V34a6 6 0 0 0 0-10z" fill="#fff"/><path d="M29 8v42M8 29h42" stroke="#1b0d55" stroke-width="2.5"/></svg>
    <h3>Platform Integrations</h3><div class="rule"></div><p>Sed ut perspiciatis unde omnis iste natus error sit voluptatem accusantium</p><div class="bar"></div></div>
  <div class="card filled" style="left:858px;top:1043px">
    <svg viewBox="0 0 58 54" aria-hidden="true"><path d="M29 8a14 14 0 0 0-8 25v7h16v-7a14 14 0 0 0-8-25z" fill="#fff"/><rect x="22" y="43" width="14" height="4" fill="#fff"/><rect x="24" y="49" width="10" height="3" fill="#fff"/><path d="M29 1v4M10 8l3 3M48 8l-3 3M4 22h5M49 22h5" stroke="#fff" stroke-width="2.5"/><circle cx="29" cy="22" r="5" fill="#3d1c9e"/></svg>
    <h3>Technology Licensing</h3><div class="rule"></div><p>Sed ut perspiciatis unde omnis iste natus error sit voluptatem accusantium</p><div class="bar"></div></div>
</section>

<section>
  <div class="abs" style="left:110px;top:1358px;width:463px;height:367px;background:
    radial-gradient(circle at 360px 110px,rgba(235,150,120,.75) 0,rgba(180,90,90,.35) 90px,transparent 170px),
    radial-gradient(circle at 110px 60px,rgba(150,60,90,.6) 0,transparent 140px),
    radial-gradient(ellipse 260px 120px at 230px 330px,rgba(120,150,210,.55) 0,transparent 100%),
    linear-gradient(135deg,#2a1c55 0%,#4a2a5e 45%,#1e2c58 100%)" role="img" aria-label="Finger touching a tablet with floating messaging and music icons"></div>
  <h2 class="abs section-title" style="left:632px;top:1382px">OUR REVOLUTIONARY PLATFORM</h2>
  <p class="abs copy" style="left:632px;top:1434px;width:457px">Whether you're marketing software, selling a product, or looking to close a deal – find out your target market and quickly modify your campaigns to reach consumers silently and securely.</p>
  <p class="abs copy" style="left:632px;top:1544px;width:457px">Our platform goes far beyond basic ad optimization to deliver individualized content that immediately increases engagement over any communication medium with embedded tones.</p>
  <div class="btn" style="left:633px;top:1648px;width:152px">Learn More <svg><use href="#go"/></svg></div>
</section>

<section>
  <h2 class="abs section-title" style="left:0;width:1200px;text-align:center;top:1809px">AWARDS</h2>
  <div class="badge" style="left:162px" role="img" aria-label="Entrepreneur award badge"></div>
  <div class="badge" style="left:412px;width:150px" role="img" aria-label="Innovation award badge"></div>
  <div class="badge" style="left:652px;width:150px" role="img" aria-label="Industry 30 under 30 listing badge"></div>
  <div class="badge" style="left:884px" role="img" aria-label="Industry 40 under 40 listing badge"></div>

  <h2 class="abs section-title" style="left:0;width:1200px;text-align:center;top:2100px">OUR CUSTOMERS &amp; PARTNERS</h2>
  <div class="abs partners">
    <div class="partner">Coral Arts Week</div>
    <div class="partner">Nordvault</div>
    <div class="partner" style="letter-spacing:2px;font-weight:500">LUMEN &amp; REYES</div>
    <div class="partner">Greyline Ltd</div>
  </div>
</section>

<section>
  <h2 class="abs section-title" style="left:109px;top:2405px">ABOUT US</h2>
  <p class="abs copy" style="left:109px;top:2454px;width:458px">VELKO™ Technology is a revolutionary platform that uses high frequency tones (known as VELKO packets) imperceptible to the human ear. VELKO's patented technology embeds information on an audio file for a more targeted, enhanced user experience via music, video, text, virtual reality, augmented reality, and other content. It is a modern-day solution to an age-old problem–establishing two-way communication with a consumer rather than listening to what they have to say.</p>
  <div class="btn" style="left:110px;top:2695px;width:152px">Learn More <svg><use href="#go"/></svg></div>
  <div class="abs" style="left:625px;top:2381px;width:462px;height:367px;background:
    radial-gradient(ellipse 200px 260px at 330px 190px,rgba(120,130,230,.55) 0,transparent 100%),
    radial-gradient(circle at 60px 40px,rgba(90,90,210,.6) 0,transparent 180px),
    linear-gradient(135deg,#3d3fb0 0%,#2c2c92 50%,#1c1a6a 100%)" role="img" aria-label="Illustration of a phone and payment card protected by a security shield"></div>
</section>

<footer class="abs footer">
  <div class="abs logo" style="left:110px;top:62px;font-size:46px">VELKO</div>
  <div class="abs contact" style="left:110px;top:133px">1-800-555-0142<br>hello@velkotech.io<br>147 , Lorem Ipsum Dolor<br>United States</div>

  <div class="abs f-head" style="left:385px;top:70px">Quick Links</div>
  <ul class="abs f-list" style="left:385px;top:97px"><li>Home</li><li>How it works</li><li>VELKO Applications</li><li>Company</li><li>Contact Us</li></ul>

  <div class="abs f-head" style="left:573px;top:70px">Subscribe to our Newsletter</div>
  <div class="abs" style="left:573px;top:113px;width:249px;height:40px;background:#fff;border-radius:3px;color:#666;font-size:14px;padding:11px 14px">Email *</div>
  <div class="abs" style="left:573px;top:165px;width:249px;height:40px;background:var(--orange);border-radius:3px;color:#fff;font:700 14px 'Roboto',sans-serif;text-align:center;line-height:40px">SUBMIT NOW</div>

  <div class="abs f-head" style="left:918px;top:70px">Follow Us On</div>
  <div class="abs social" style="left:918px;top:114px" aria-label="Social media links"><span></span><span></span><span></span><span></span></div>

  <div class="abs" style="left:111px;top:315px;width:976px;height:1px;background:var(--line)"></div>
  <div class="abs" style="left:0;top:342px;width:1200px;text-align:center;font-size:14px;color:var(--white)">©2022 VELKO™. All Rights Reserved</div>
</footer>

</body>
</html>
```